PIPE RELINING COMPANY NEEDS A NEW INFORMATIVE FLYER CREATED

We are a company that sells a service to residential homeowners (using a particular state of the art international product) and we need to refresh our A4 tri- fold flyer (z fold 6 pages). The layout needs to include pictures, heading and text boxes, but be simple and clean cut at the same time.

The front of the flyer must have the attached picture of the pipe under the house, logo and website.

This flyer is going to be given to clients and to leave with them when we quote for work.

Our colour scheme is black, white, red. A highlight colour if needed (in small amounts) could be 100% cyan and also a bright orange.

I have attached the copy of the text and this can be spread out throughout the brochure.

We are a professional and industry leading company so it needs to be professional, clean cut but with a modern edge.

Target Market(s)

HOMEOWNERS

Industry/Entity Type

It Company

Font styles to use
Sans Serif

Colors
ec1f27
ffffff
000000
f37122

Requirements
Must have
• PROFESSINAL, MODERN
• USE OF BLACK, RED AND WHITE - REFER LOGO
Should not have
• BE CLUTTERED

```html
<!DOCTYPE html>
<html lang="en">
<head>
<meta charset="utf-8">
<title>Pipe Relining Flyer – Inside Spread</title>
<link href="https://fonts.googleapis.com/css2?family=Ubuntu:wght@300;400;500&display=swap" rel="stylesheet">
<style>
  :root{
    --red:#ec1f27;
    --orange:#f37122;
    --ink:#1d1d1d;
    --white:#ffffff;
    --terracotta:#d98a63;
    --liner-green:#4faa46;
    --pipe-rose:#b98b7d;
  }
  *{box-sizing:border-box;margin:0;padding:0}
  html,body{width:1200px;height:848px;overflow:hidden;background:var(--white)}
  .spread{position:relative;width:1200px;height:848px;overflow:hidden;
    font-family:"Ubuntu",Arial,sans-serif;font-weight:300;color:var(--ink);
    font-size:13.6px;line-height:20px}
  .backdrop{position:absolute;inset:0;width:1200px;height:848px}
  .base-band{position:absolute;left:0;bottom:0;width:1200px;height:16px;background:var(--orange)}
  .tab{position:absolute;height:25px;background:var(--red);color:var(--white);
    font-weight:500;font-size:14px;line-height:25px;padding-left:20px;
    border-radius:0 6px 6px 0}
  .tab.inset{border-radius:4px;padding-left:8px}
  .block{position:absolute;text-align:justify}
  .bullets{list-style:none}
  .bullets li{position:relative;padding-left:26px}
  .bullets li::before{content:"";position:absolute;left:2px;top:7px;width:6px;height:6px;background:var(--red)}
  .block p{text-indent:24px}
  .benefits{font-size:14px;line-height:23px;text-align:left}
  .benefits p{text-indent:10px}
  .benefits p.flush{text-indent:0}
  .benefits b{font-weight:500}
  .pipe-sample{position:absolute;left:1070px;top:12px;width:122px;height:120px;border-radius:6px;
    background:linear-gradient(135deg,var(--terracotta),var(--liner-green))}
  .shot{position:absolute;top:668px;width:99px;height:102px;border:1px solid #333;border-radius:3px}
  .shot.before{left:880px;background:linear-gradient(160deg,#d3b1a4,var(--pipe-rose))}
  .shot.after{left:1021px;background:linear-gradient(160deg,#6cbd4e,#3f8f35)}
  .caption{position:absolute;top:780px;width:99px;text-align:center;font-weight:500;font-size:16px}
</style>
</head>
<body>
<main class="spread">
  <svg class="backdrop" viewBox="0 0 1200 848" role="img" aria-label="Faded photographs of a suburban house, lawn and exposed tree roots behind diagonal white bands">
    <defs>
      <linearGradient id="house" x1="0" y1="0" x2="0" y2="1">
        <stop offset="0" stop-color="#e6e8e4"/><stop offset=".6" stop-color="#d4d9cf"/><stop offset="1" stop-color="#c3cdb4"/>
      </linearGradient>
      <linearGradient id="roots" x1="0" y1="0" x2="0" y2="1">
        <stop offset="0" stop-color="#e4e2dc"/><stop offset="1" stop-color="#cfc9bd"/>
      </linearGradient>
    </defs>
    <rect width="1200" height="848" fill="#fafafa"/>
    <polygon points="0,60 260,0 1010,0 1010,250 600,848 0,848" fill="url(#house)" opacity=".55"/>
    <polygon points="100,848 520,330 1000,330 840,848" fill="url(#roots)" opacity=".6"/>
    <polygon points="1010,0 1200,0 1200,848 1010,848" fill="url(#house)" opacity=".35"/>
    <polygon points="0,0 400,0 0,360" fill="#ffffff" opacity=".85"/>
    <polygon points="60,848 400,420 420,848" fill="#ffffff" opacity=".55"/>
    <polygon points="400,0 800,0 800,848 400,848" fill="#ffffff" opacity=".6"/>
    <polygon points="800,0 1200,0 1200,848 800,848" fill="#ffffff" opacity=".55"/>
    <polygon points="1010,0 1200,0 1200,220" fill="#ffffff" opacity=".6"/>
    <polygon points="800,300 1200,620 1200,848 800,848" fill="#ffffff" opacity=".6"/>
    <circle cx="663" cy="446" r="38" fill="none" stroke="#ffffff" stroke-width="3" opacity=".8"/>
    <circle cx="663" cy="446" r="14" fill="none" stroke="#ffffff" stroke-width="2" opacity=".8"/>
  </svg>

  <ul class="block bullets" style="left:20px;top:16px;width:364px">
    <li>Sewers back up in properties due to ageing lines, misaligned joints, root infestation, calcification and ground movement, costing property owners thousands of dollars in damage to their homes and landscaping.</li>
    <li>Pipe relining eliminates the need for costly excavations to expose and replace this damaged pipework.</li>
    <li>Pipe Relining is the process of installing a new pipe within the old.</li>
    <li>Why replace all of your drainage pipes when you can permanently repair the broken sections without destroying your environment.</li>
  </ul>

  <div class="tab" style="left:0;top:274px;width:240px">What Does Pipe Relining Mean?</div>
  <div class="block" style="left:20px;top:316px;width:364px">
    <p>Pipe relining is the method of repairing existing pipe work from within the pipe itself. This is done by using the latest technology to insert a strong internal liner inside the existing pipe.</p>
    <p>During this process the resin impregnated side of the liner is pressed against the wall of the original host pipe at a specified pressure. This pressure ensure 100% resin contact and extrudes resin into all pipe joints, cracks and breaks ensuring no future tree root ingress or pipe movement is possible.</p>
    <p>Pipe relining can be undertaken in either short sectional repair, or long lengths utilising the inversion relining method.</p>
  </div>

  <div class="tab" style="left:0;top:593px;width:312px">Which Problems Can Pipe Relining Repair?</div>
  <div class="block" style="left:20px;top:634px;width:364px">
    <p>Pipe relining can repair broken, cracked or root infested pipes, pipes with missing sections and pipes that continually block.</p>
  </div>
  <div class="block" style="left:20px;top:714px;width:364px">
    <p>No matter if the pipes are vertical, horizontal or concealed, they all can be repaired. Sections of broken pipes can be relined, without having to replace the entire pipeline.</p>
  </div>

  <div class="tab inset" style="left:400px;top:16px;width:176px">Patch Repair Process</div>
  <ul class="block bullets" style="left:414px;top:60px;width:368px">
    <li>Clean the line with a high pressure water jetter, and carry out a camera inspection to determine the exact location and cause of the problems.</li>
    <li>Prepare the liner. Cut the liner to the correct length, mix the appropriate amount of rein and impregnate the rein into the liner.</li>
    <li>Invert the liner into the pipe, inflate and then cure.</li>
    <li>A seamless, flexible liner is cut to length and filled with environmentally safe epoxy rein. The liner is them inverted into the existing, host pipe and inflated using compressed air. Once the liner is fully cured with hot water, it is ready for use.</li>
    <li>The result is a completely new pipe inside the old. This pipe within a pie is 100% water tight, stronger than PVC pipe, and has an increased flow rate compared to most existing pipes. Relined pipes have a life expectancy of 50 years and our installation work has a 25 year guarantee.</li>
  </ul>

  <div class="tab inset" style="left:414px;top:436px;width:178px">Benefits of Pipe Relining</div>
  <div class="block benefits" style="left:414px;top:480px;width:368px">
    <p><b>Quick Installation</b> – Most relining jobs can be completed in the same day-without tht mess and disruption of excavation.</p>
    <p><b>Long Life Product</b> – Pipe Relining is a long term solution with a 50 year life expectancy.</p>
    <p class="flush">Minimal Disruption – ave your landscapes, trees and driveways.</p>
    <p><b>Economical</b> – Save on the cost, time and hassle of restoring your property and landscaping.</p>
    <p><b>Installation Guarantee</b> – ClearBore offer a 25 year warranty, twice that of standard excavations. This also includes an annual warranty camera inspection.</p>
    <p class="flush">Provides a solution to the whole problem, not just temporary relief from the symptoms.</p>
  </div>

  <div class="pipe-sample" role="img" aria-label="Photo of a cut-away terracotta pipe with a green liner inside"></div>
  <div class="tab inset" style="left:815px;top:16px;width:227px">What Does Pipe Relining Mean?</div>
  <ul class="block bullets" style="left:815px;top:60px;width:368px;text-align:left">
    <li>Permanent jointless liner</li>
    <li>50 years life expectancy</li>
    <li>Up front price</li>
    <li>Environmentally sound</li>
    <li>Eliminates structural disturbances</li>
    <li>Imprevious to future root penetration</li>
    <li>Provides increased flow characteristics</li>
    <li style="text-align:justify">Suitable for industrial, residential and commercial applications</li>
  </ul>

  <div class="tab inset" style="left:815px;top:257px;width:227px">Things You Should Know</div>
  <ul class="block bullets" style="left:815px;top:300px;width:368px">
    <li>Knowledge &amp; Experience</li>
    <li>We train other plumbers and have been doing it for over 10 years.</li>
    <li>We’re An Owned &amp; Operated Business</li>
    <li>We take great pride in our work. Our business is based on relationships not transactions.</li>
    <li>We Use the best in class pipe relining solution</li>
    <li>We have sourced the best products and equipment from around the world and our FlexCore product is from Germany.</li>
    <li>We have state of the art equipment.</li>
    <li>Our truck is customer designed and filly equipped with latest technology to carry out pipe relining.</li>
    <li>We’re Fully licensed &amp; Insured</li>
    <li>All of our technicians are fully licensed and qualified to complete the job. Our company is fully insured and are happy to provide you with documentation.</li>
  </ul>

  <div class="shot before" role="img" aria-label="Camera photo inside a cracked pipe before relining"></div>
  <div class="shot after" role="img" aria-label="Camera photo inside a green relined pipe after relining"></div>
  <div class="caption" style="left:880px">Before</div>
  <div class="caption" style="left:1021px">After</div>

  <div class="base-band"></div>
</main>
</body>
</html>
```